Larkspur Talent IT Recruiting firm needs a business card design for Recruiters, Sourcers, and Account

We need business cards that allow us to change all contact info, names, titles (Recruiter, Sourcer, Account Manager, Director, CEO, etc) per person since we have three offices, in three cities, Phoenix, Austin, and Las Vegas. We do recruiting and contractors for IT positions (Developers, Architects, Software Engineers, Security Engineers, Help Desk, DBAs, PMs, Scrum Masters, etc.) Our client companies are very diverse from Meridian 100 to silicone Valley type start-ups.

So, while we what hip, techie, and quirky, it still needs to be professional. Primary color we use is blue, with silver as a secondary color.

Target Market(s)

IT, Technology

Industry/Entity Type

Business

Contact Information for Business Card

Company name: Larkspur Talent, Inc.
Website: www.larkspurtalent.example
Logos for Careerloop, Blipster, and Myriada

Name, Title, Office Number, Cell Number, email

Font styles to use
Serif
Sans Serif

Colors
0455a3
d5d5d5

Requirements
Nice to have
• The grey I selected below is not necessary - but, would like silver included. I included a card design (File 3: LTI early trial example.jpg) that I had started on. It's very rough, and not quite what we're looking for, but what we did like is the logo, big, maybe a bit faded, off center, goes out of frame, etc. Still looking for other ideas - you are the pros! But, just an idea of a design element we liked.

```html
<!DOCTYPE html>
<html lang="en">
<head>
<meta charset="utf-8">
<title>Larkspur Talent – Business Card, Front and Back</title>
<link rel="stylesheet" href="https://fonts.googleapis.com/css2?family=Questrial&family=PT+Sans:wght@400;700&family=Marcellus+SC&display=swap">
<style>
  :root {
    --stage: #000000;
    --card: #ffffff;
    --brand-blue: #0455a3;
    --ink: #222222;
    --muted: #555555;
    --emblem-top: #b3cbee;
    --emblem-bottom: #9ca7d8;
  }
  * { box-sizing: border-box; margin: 0; padding: 0; }
  html, body {
    width: 1200px; height: 386px; overflow: hidden;
    background: var(--stage);
  }
  .stage { position: relative; width: 1200px; height: 386px; }

  .card-face {
    position: absolute; top: 42px; height: 308px;
    background: var(--card);
  }
  .card-face--front { left: 50px; width: 542px; }
  .card-face--back { left: 620px; width: 540px; }

  .emblem-layer { position: absolute; left: 0; top: 0; }

  .card-content { position: absolute; top: 42px; height: 308px; }
  .card-content--front { left: 50px; width: 542px; }
  .card-content--back { left: 620px; width: 540px; }

  .wordmark {
    position: absolute;
    font-family: "Questrial", sans-serif;
    color: var(--brand-blue);
    line-height: 1;
    text-align: right;
  }
  .wordmark__line1 { display: block; font-size: 38px; letter-spacing: 8px; margin-right: -8px; }
  .wordmark__line2 { display: block; font-size: 28px; letter-spacing: 5px; margin-right: -5px; margin-top: 4px; }
  .card-content--front .wordmark { left: 20px; top: 34px; }
  .card-content--back .wordmark { left: 216px; top: 110px; }

  .tagline {
    position: absolute;
    font-family: "Marcellus SC", serif;
    font-size: 15px; letter-spacing: 1.5px;
    color: var(--ink);
    white-space: nowrap;
  }
  .card-content--front .tagline { left: 28px; top: 113px; }
  .card-content--back .tagline { left: 216px; top: 185px; }

  .person { position: absolute; left: 24px; top: 151px; font-family: "PT Sans", sans-serif; }
  .person__name { font-size: 17px; font-weight: 700; color: var(--brand-blue); }
  .person__title { font-size: 13.5px; color: var(--muted); margin-top: 4px; }

  .contact-list {
    position: absolute; left: 24px; top: 206px; list-style: none;
    font-family: "PT Sans", sans-serif; font-size: 13.5px; color: var(--ink);
  }
  .contact-list li { display: flex; align-items: center; height: 22px; white-space: nowrap; }
  .contact-list svg { width: 12px; height: 12px; margin-right: 6px; flex: none; }
  .contact-list .social { gap: 14px; margin-top: 5px; }
  .social__item { display: flex; align-items: center; }
  .social__dot {
    width: 15px; height: 15px; border-radius: 50%;
    background: var(--brand-blue); margin-right: 5px; flex: none;
  }

  .website {
    position: absolute; left: 224px; top: 226px;
    font-family: "Questrial", sans-serif;
    font-size: 16px; letter-spacing: 2.4px; color: var(--ink);
    white-space: nowrap;
  }
</style>
</head>
<body>
<main class="stage">
  <div class="card-face card-face--front"></div>
  <div class="card-face card-face--back"></div>

  <svg class="emblem-layer" width="1200" height="386" viewBox="0 0 1200 386">
    <defs>
      <clipPath id="card-area">
        <rect x="50" y="42" width="542" height="308"/>
        <rect x="620" y="42" width="540" height="308"/>
      </clipPath>
      <linearGradient id="emblem-fade" x1="0" y1="0" x2="0" y2="1">
        <stop offset="0" stop-color="#b3cbee"/>
        <stop offset="1" stop-color="#9ca7d8"/>
      </linearGradient>
    </defs>
    <g clip-path="url(#card-area)">
      <circle cx="607" cy="205" r="174" fill="url(#emblem-fade)" opacity="0.9"
              role="img" aria-label="Large faded brand emblem spanning both card faces"/>
    </g>
  </svg>

  <section class="card-content card-content--front" aria-label="Card front">
    <div class="wordmark">
      <span class="wordmark__line1">LARKSPUR</span>
      <span class="wordmark__line2">TALENT</span>
    </div>
    <p class="tagline">BUILDING TEAMS THAT FIT</p>
    <div class="person">
      <p class="person__name">Mara Ellison</p>
      <p class="person__title">First Touch Embassador</p>
    </div>
    <ul class="contact-list">
      <li>
        <svg viewBox="0 0 12 12" aria-hidden="true"><path d="M3 1 L5 3.5 L4 5 Q5.5 7.5 7 8 L8.5 7 L11 9 L9.5 11 Q3 10 1 2.5 Z" fill="var(--brand-blue)"/></svg>
        555-014-2273
      </li>
      <li>
        <svg viewBox="0 0 12 12" aria-hidden="true"><rect x="1" y="2.5" width="10" height="7" rx="1" fill="var(--brand-blue)"/><path d="M1.5 3 L6 6.5 L10.5 3" stroke="#fff" stroke-width="1" fill="none"/></svg>
        mara@larkspurtalent.example
      </li>
      <li>
        <svg viewBox="0 0 12 12" aria-hidden="true"><circle cx="6" cy="6" r="5" fill="none" stroke="var(--brand-blue)" stroke-width="1.2"/><ellipse cx="6" cy="6" rx="2.2" ry="5" fill="none" stroke="var(--brand-blue)" stroke-width="1"/><path d="M1 6 H11" stroke="var(--brand-blue)" stroke-width="1"/></svg>
        www.larkspurtalent.example
      </li>
      <li class="social">
        <span class="social__item"><span class="social__dot" role="img" aria-label="Blipster"></span>@MaraEllisonLT</span>
        <span class="social__item"><span class="social__dot" role="img" aria-label="Careerloop"></span>@MaraEllisonLT</span>
      </li>
    </ul>
  </section>

  <section class="card-content card-content--back" aria-label="Card back">
    <div class="wordmark">
      <span class="wordmark__line1">LARKSPUR</span>
      <span class="wordmark__line2">TALENT</span>
    </div>
    <p class="tagline">BUILDING TEAMS THAT FIT</p>
    <p class="website">www.larkspurtalent.example</p>
  </section>
</main>
</body>
</html>
```